New Business Card Design Project

We would like a business card that represents the sale of boat, home, auto, and life insurance.

The logo can change colors to meet the look of the design if needed.

Industry/Entity Type

Business

```html
<!DOCTYPE html>
<html lang="en">
<head>
<meta charset="utf-8">
<title>Halden Financial — Business Card</title>
<link rel="stylesheet" href="https://fonts.googleapis.com/css2?family=Open+Sans:wght@400;600&display=swap">
<style>
  :root {
    --backdrop: #4a4a4a;
    --card: #ffffff;
    --teal: #3b7489;
    --teal-text: #ffffff;
    --ink: #2e3236;
  }
  * { margin: 0; padding: 0; box-sizing: border-box; }
  html, body { width: 1200px; height: 676px; overflow: hidden; }
  body {
    background: var(--backdrop);
    font-family: "Open Sans", Arial, sans-serif;
    position: relative;
  }
  .card {
    position: absolute;
    top: 195px;
    width: 500px;
    height: 286px;
    background: var(--card);
    overflow: hidden;
    box-shadow: 0 6px 18px rgba(0,0,0,0.35);
  }
  .card--front { left: 70px; }
  .card--back { left: 630px; }

  .brand {
    position: absolute;
    display: flex;
    align-items: center;
    gap: 10px;
  }
  .brand__dot {
    width: 14px; height: 14px;
    border-radius: 50%;
    background: var(--teal);
  }
  .brand__name {
    color: var(--teal);
    font-weight: 600;
    font-size: 17px;
    letter-spacing: 0.18em;
    text-transform: uppercase;
    white-space: nowrap;
  }
  .card--front .brand { left: 36px; top: 48px; }
  .card--back .brand { left: 50%; top: 92px; transform: translateX(-50%); }

  .band {
    position: absolute;
    left: 0; right: 0; bottom: 0;
    background: var(--teal);
    color: var(--teal-text);
  }
  .card--front .band { height: 122px; }
  .card--back .band { height: 96px; }

  .identity {
    position: absolute;
    right: 30px; top: 22px;
    font-size: 15px;
    letter-spacing: 0.02em;
  }
  .identity__role { font-size: 13px; }

  .contacts {
    display: flex;
    justify-content: space-between;
    padding: 22px 26px 0;
    font-size: 12.5px;
  }
  .contacts__col { display: flex; flex-direction: column; gap: 8px; }
  .contact { display: flex; align-items: flex-start; gap: 7px; line-height: 1.3; }
  .contact svg { flex: none; width: 11px; height: 11px; margin-top: 3px; }
</style>
</head>
<body>

<section class="card card--front">
  <div class="brand">
    <span class="brand__dot"></span>
    <span class="brand__name">Halden Financial</span>
  </div>
  <div class="band">
    <p class="identity">YOUR NAME &nbsp;/ <span class="identity__role">designation</span></p>
  </div>
</section>

<section class="card card--back">
  <div class="brand">
    <span class="brand__dot"></span>
    <span class="brand__name">Halden Financial</span>
  </div>
  <div class="band">
    <div class="contacts">
      <div class="contacts__col">
        <p class="contact">
          <svg viewBox="0 0 12 12"><path fill="#fff" d="M3 1h2l1 3-1.5 1a6 6 0 0 0 2.5 2.5L8 6l3 1v2a2 2 0 0 1-2 2A8 8 0 0 1 1 3a2 2 0 0 1 2-2z"/></svg>
          0123 456 789
        </p>
        <p class="contact">
          <svg viewBox="0 0 12 12"><rect x="1.5" y="1.5" width="9" height="9" fill="none" stroke="#fff" stroke-width="1.4"/></svg>
          0123 456 789
        </p>
      </div>
      <div class="contacts__col">
        <p class="contact">
          <svg viewBox="0 0 12 12"><rect x="1" y="2.5" width="10" height="7" fill="#fff"/><path d="M1 2.5l5 4 5-4" fill="none" stroke="#3b7489" stroke-width="1"/></svg>
          youremail@mail.com
        </p>
        <p class="contact">
          <svg viewBox="0 0 12 12"><circle cx="6" cy="6" r="4.8" fill="none" stroke="#fff" stroke-width="1.2"/><path d="M1.2 6h9.6M6 1.2c-2.4 3-2.4 6.6 0 9.6M6 1.2c2.4 3 2.4 6.6 0 9.6" fill="none" stroke="#fff" stroke-width="0.9"/></svg>
          www.yourwebsite.com
        </p>
      </div>
      <div class="contacts__col">
        <p class="contact">
          <svg viewBox="0 0 12 12"><path fill="#fff" d="M6 0.5a4 4 0 0 1 4 4c0 3-4 7-4 7s-4-4-4-7a4 4 0 0 1 4-4z"/><circle cx="6" cy="4.5" r="1.5" fill="#3b7489"/></svg>
          <span>address (street address<br>suite number, city, state, zip</span>
        </p>
      </div>
    </div>
  </div>
</section>

</body>
</html>
```